Business card

We need a business card design for our company based in Auckland , New Zealand called 'Ridge + Studio Ltd'. We provide architectural services. We would like to see designs that use the max. three colours (such as white, black, grey) The final design should communicate financial safety and growth."
Also I will provide our company logo. I would like to the logo to be embeded onto our business card.

Target Market(s)

new residential house, alteration & addition & light commericila design & drafting service

Industry/Entity Type

Architecture

Contact Information for Business Card

Company name: ridge + studio Ltd.
Name: Mark Delford
Job title: architectural designer & Design LBP
email address: mark@rplusd.co.nz
mobile number: 02 5163 2290
web site: www.rplusd.co.nz

Requirements
Must have
• My project must have..
• - embeded logo (attached company logo)
• I don't have a bigger version for our company logo, but I have one old one, so you can remove the word from it)
• - insert the attached small BKTW logo & LBP logo
• - creative, simple and clear business card.
• - Max. three colours
Nice to have
• - Here are the samples I would like to share with you: http://www.plimvora.com/blog/minimalistic-business-card-designs/
• I would like to have my business card like one of the creation.
Should not have
• TBA

```html
<!DOCTYPE html>
<html lang="en">
<head>
<meta charset="UTF-8">
<title>Ridge + Studio Ltd — Business Card</title>
<link rel="stylesheet" href="https://fonts.googleapis.com/css2?family=Open+Sans:wght@600;700&display=swap">
<style>
  :root {
    --ink: #111111;
    --grey: #bdbdbd;
    --rule: #d6d6d6;
    --badge: #5d6a60;
    --paper: #ffffff;
    --backdrop: #ffffff;
  }
  * { margin: 0; padding: 0; box-sizing: border-box; }
  html, body {
    width: 1200px;
    height: 1200px;
    overflow: hidden;
    background: var(--backdrop);
  }
  .card {
    position: absolute;
    left: 182px;
    width: 841px;
    height: 504px;
    background: var(--paper);
    border: 1px solid #e6e6e6;
  }
  .card--front { top: 57px; }
  .card--back { top: 634px; height: 497px; }

  /* Front */
  .brand-square {
    position: absolute;
    left: 186px;
    top: 201px;
    width: 48px;
    height: 48px;
    background: var(--grey);
  }
  .divider {
    position: absolute;
    width: 2px;
    background: var(--rule);
  }
  .card--front .divider { left: 362px; top: 137px; height: 175px; }
  .brand-name {
    position: absolute;
    left: 406px;
    top: 180px;
    font-family: "Open Sans", sans-serif;
    font-weight: 600;
    font-size: 34px;
    line-height: 44px;
    color: var(--ink);
  }

  /* Back */
  .member-badge {
    position: absolute;
    left: 75px;
    top: 48px;
    width: 150px;
    height: 127px;
  }
  .practitioner-badge {
    position: absolute;
    left: 72px;
    top: 296px;
    width: 136px;
    height: 136px;
  }
  .card--back .divider { left: 367px; top: 163px; height: 154px; }
  .contact {
    position: absolute;
    left: 429px;
    top: 160px;
    font-family: "Open Sans", sans-serif;
    color: var(--ink);
  }
  .contact__name {
    font-size: 26px;
    font-weight: 700;
    line-height: 32px;
  }
  .contact__title {
    font-size: 18px;
    font-weight: 700;
    line-height: 26px;
    margin-bottom: 18px;
  }
  .contact__list { list-style: none; }
  .contact__row {
    display: flex;
    font-size: 18px;
    font-weight: 600;
    line-height: 26px;
  }
  .contact__label { width: 117px; }
</style>
</head>
<body>

<section class="card card--front" aria-label="Card front">
  <div class="brand-square" aria-hidden="true"></div>
  <div class="divider"></div>
  <p class="brand-name">Ridge +<br>Studio Ltd</p>
</section>

<section class="card card--back" aria-label="Card back">
  <svg class="member-badge" viewBox="0 0 150 127" role="img" aria-label="Professional member badge">
    <rect x="0" y="0" width="150" height="127" fill="var(--badge)"/>
  </svg>
  <svg class="practitioner-badge" viewBox="0 0 136 136" role="img" aria-label="Licensed practitioner badge">
    <circle cx="68" cy="68" r="66" fill="var(--ink)"/>
  </svg>
  <div class="divider"></div>
  <div class="contact">
    <p class="contact__name">Mark Delford</p>
    <p class="contact__title">Architectural Designer &amp; Design LBP</p>
    <ul class="contact__list">
      <li class="contact__row"><span class="contact__label">T</span><span>02 5163 2290</span></li>
      <li class="contact__row"><span class="contact__label">M</span><span>mark@rplusd.co.nz</span></li>
      <li class="contact__row"><span class="contact__label">W</span><span>www.rplusd.co.nz</span></li>
    </ul>
  </div>
</section>

</body>
</html>
```